Brochure for a website accessibility report

This brochure is related to a report that www.qelvantrix.org sell. The report shows the results of an automated audit of a websites accessibility. It shows details of issues found with screen shots, examples of code and provides remediation advice.

The brochure will be a pdf 8.5 inches by 11 inches. It can be anywhere from 6 to 10 pages.

The FlintVue™ name itself should be “Bree Serif” font. The fonts, styles, colors and sizes are up to you.

The images used and logo of the Office of Digital Reachworks and K7P logo are upload

We highlighted in blue page extracts from the report we sell. Do not use the blue highlight, it is merely there to show you where the specific examples of the report we sell are vs the other content in the report. The areas in blue which show the content from the actual report should be shown as an extract of the actual page of the report. You have flexibility to change the layout and the way the content look.

The red square callouts over the blue content are callouts that describe the specific page extracts. We used it as a red callout only so that you would be able to see it. You should change the specific location, look and feel of the callout to be appropriate

Target Market(s)

Marketing and Technical people

Industry/Entity Type

Information Technology

Font styles to use
Sans Serif

Colors

Designer to choose colors to be used in the design.

Requirements
Should not have
• wheelchairs, images of blind people

```html
<!DOCTYPE html>
<html lang="en">
<head>
<meta charset="utf-8">
<title>Accessibility Report Brochure – Section 1</title>
<link href="https://fonts.googleapis.com/css2?family=EB+Garamond:wght@400&family=Oswald:wght@600&family=Poppins:wght@300;400;500;600&display=swap" rel="stylesheet">
<style>
  :root {
    --bg: #dcdcdc;
    --paper: #ffffff;
    --red: #a4221f;
    --red-bright: #d3263a;
    --charcoal: #3a3a3a;
    --ink: #222222;
    --muted: #555555;
    --green: #2daa5a;
    --green-bar: #3aa845;
    --yellow: #e6b62a;
    --blue: #2f9fd8;
    --lime: #7dbb3f;
    --illustration: #c9d6e0;
  }
  * { box-sizing: border-box; margin: 0; padding: 0; }
  html, body { width: 1200px; height: 900px; overflow: hidden; background: var(--bg); }
  .page {
    position: absolute; left: 267px; top: 20px;
    width: 665px; height: 860px;
    background: var(--paper); overflow: hidden;
    box-shadow: 0 4px 18px rgba(0,0,0,.12);
    font-family: "Poppins", sans-serif; color: var(--ink);
  }
  .page-stripe { position: absolute; left: 0; right: 0; bottom: 0; height: 9px; background: var(--green); }
  .hero-arcs { position: absolute; left: 0; top: 0; }
  .hero-illustration {
    position: absolute; left: 15px; top: 45px; width: 400px; height: 400px; border-radius: 50%;
    background: radial-gradient(circle at 45% 45%, #f1e6d2 0%, var(--illustration) 70%);
    border: 1.5px solid var(--ink);
  }
  .brand {
    position: absolute; left: 462px; top: 72px;
    font-family: "Poppins", sans-serif; font-weight: 500; font-size: 12px;
    color: var(--ink); white-space: nowrap;
  }
  .section-intro { position: absolute; left: 490px; top: 270px; width: 160px; }
  .section-title {
    font-family: "Oswald", sans-serif; font-weight: 600; font-size: 30px; letter-spacing: .5px;
    border-bottom: 2px dotted var(--ink); padding-bottom: 4px; margin-bottom: 8px;
  }
  .section-text { font-family: "EB Garamond", serif; font-size: 14px; line-height: 1.25; }
  .chart-heading { position: absolute; left: 40px; top: 530px; width: 600px; }
  .chart-title { color: var(--red-bright); font-weight: 600; font-size: 17px; }
  .chart-note { font-size: 10.5px; font-weight: 300; color: var(--muted); line-height: 1.4; width: 560px; }
  .wheel { position: absolute; left: 10px; top: 600px; }
  .principle {
    position: absolute; left: 255px; width: 110px; font-size: 9.5px; font-weight: 500;
    letter-spacing: .3px; border-bottom: 1.5px dotted currentColor; padding-bottom: 1px;
  }
  .principle--perceivable { top: 612px; color: var(--red-bright); }
  .principle--operable { top: 669px; color: var(--yellow); }
  .principle--understandable { top: 720px; color: var(--blue); }
  .principle--robust { top: 754px; color: var(--lime); }
  .guidelines, .issues { position: absolute; top: 596px; list-style: none; }
  .guidelines { left: 372px; width: 155px; }
  .guidelines li, .issues li { height: 17px; font-size: 9px; font-weight: 300; line-height: 17px; white-space: nowrap; }
  .guidelines li { padding-left: 6px; border-left: 1.5px dotted var(--gl); }
  .gl-p { --gl: var(--red-bright); } .gl-o { --gl: var(--yellow); } .gl-u { --gl: var(--blue); } .gl-r { --gl: var(--lime); }
  .issues-bar {
    position: absolute; left: 530px; top: 591px; width: 18px; height: 197px; background: var(--green-bar);
    display: flex; align-items: center; justify-content: center;
  }
  .issues-bar span {
    writing-mode: vertical-rl; color: #fff; font-size: 8.5px; font-weight: 500; letter-spacing: 1px;
  }
  .issues { left: 556px; }
  .issues li { font-size: 8.5px; word-spacing: 3px; }
</style>
</head>
<body>
<main class="page">
  <svg class="hero-arcs" width="665" height="560" viewBox="0 0 665 560" aria-hidden="true">
    <path d="M194.8 13.9 A232 232 0 1 1 81.9 435" fill="none" stroke="var(--red)" stroke-width="62"/>
    <path d="M167.6 -23.9 A273 273 0 0 1 424.1 69.5" fill="none" stroke="var(--charcoal)" stroke-width="22"/>
    <path d="M262.5 513.9 A273 273 0 0 1 -21.4 381.5" fill="none" stroke="var(--charcoal)" stroke-width="22"/>
  </svg>
  <div class="hero-illustration" role="img" aria-label="Illustration of a developer at a desk working across several computer monitors"></div>

  <p class="brand">Office of Digital Reachworks</p>

  <section class="section-intro">
    <h2 class="section-title">SECTION 1</h2>
    <p class="section-text">The first section of the report begins with a Summary Chart that breaks down WCAG 2.1 A/AA issues by principle:</p>
  </section>

  <header class="chart-heading">
    <h3 class="chart-title">Example WCAG 2.1 A/AA Summary Chart</h3>
    <p class="chart-note">Checkpoints with failures detected are identified in the "Issues Discovered" column. The detail behind these failures is available in the next section.</p>
  </header>

  <svg class="wheel" width="250" height="260" viewBox="0 0 250 260" aria-hidden="true">
    <path d="M38 44.2 A112 112 0 0 1 129.5 19.7 L120.8 68.9 A62 62 0 0 0 70.1 82.5 Z" fill="var(--red-bright)"/>
    <path d="M129.5 19.7 A112 112 0 0 1 207 74 L163.7 99 A62 62 0 0 0 120.8 68.9 Z" fill="var(--yellow)"/>
    <path d="M207 74 A112 112 0 0 1 215.3 168.3 L168.3 151.2 A62 62 0 0 0 163.7 99 Z" fill="var(--blue)"/>
    <path d="M215.3 168.3 A112 112 0 0 1 148.3 235.3 L131.2 188.3 A62 62 0 0 0 168.3 151.2 Z" fill="var(--lime)"/>
    <circle cx="110" cy="130" r="58" fill="#e6e6e6"/>
    <circle cx="110" cy="130" r="48" fill="#f7f7f7" stroke="#cfcfcf" stroke-width="2"/>
    <text x="110" y="135" text-anchor="middle" font-family="Poppins, sans-serif" font-weight="600" font-size="14" fill="var(--red-bright)">WCAG 2.1</text>
    <g fill="#fff">
      <circle cx="87.5" cy="46" r="7"/><circle cx="159.9" cy="58.7" r="7"/>
      <circle cx="196.7" cy="122.4" r="7"/><circle cx="171.5" cy="191.5" r="7"/>
    </g>
    <g fill="#fff" stroke-width="2">
      <circle cx="81" cy="21.8" r="15" stroke="var(--red-bright)"/>
      <circle cx="174.3" cy="38.3" r="15" stroke="var(--yellow)"/>
      <circle cx="221.6" cy="120.2" r="15" stroke="var(--blue)"/>
      <circle cx="189.2" cy="209.2" r="15" stroke="var(--lime)"/>
    </g>
    <g font-family="Poppins, sans-serif" font-size="11" text-anchor="middle">
      <text x="81" y="25.8" fill="var(--red-bright)">01</text>
      <text x="174.3" y="42.3" fill="var(--yellow)">02</text>
      <text x="221.6" y="124.2" fill="var(--blue)">03</text>
      <text x="189.2" y="213.2" fill="var(--lime)">04</text>
    </g>
  </svg>

  <span class="principle principle--perceivable">PERCEIVABLE</span>
  <span class="principle principle--operable">OPERABLE</span>
  <span class="principle principle--understandable">UNDERSTANDABLE</span>
  <span class="principle principle--robust">ROBUST</span>

  <ul class="guidelines">
    <li class="gl-p">Guideline 1.1 Text Alternatives</li>
    <li class="gl-p">Guideline 1.2 Time-based Media</li>
    <li class="gl-p">Guideline 1.3 Adaptable</li>
    <li class="gl-p">Guideline 1.4 Distinguishable</li>
    <li class="gl-o">Guideline 2.1 Keyboard Accessible</li>
    <li class="gl-o">Guideline 2.2 Enough Time</li>
    <li class="gl-o">Guideline 2.4 Navigable</li>
    <li class="gl-u">Guideline 3.1 Readable</li>
    <li class="gl-u">Guideline 3.2 Predictable</li>
    <li class="gl-u">Guideline 3.3 Input Assistance</li>
    <li class="gl-r">Guideline 4.1 Compatible</li>
  </ul>

  <div class="issues-bar"><span>ISSUES DISCOVERED</span></div>

  <ul class="issues">
    <li>1.1.1</li>
    <li>1.2.1 1.2.2 1.2.3 1.2.4 1.2.5</li>
    <li>1.3.1 1.3.2 1.3.5</li>
    <li>1.4.1 1.4.3 1.4.4 1.4.11</li>
    <li>2.1.1 2.1.2</li>
    <li>2.2.1 2.2.2</li>
    <li>2.4.1 2.4.2 2.4.4 2.4.7</li>
    <li>3.1.1</li>
    <li>3.2.1 3.2.2</li>
    <li>3.3.2</li>
    <li>4.1.1 4.1.2</li>
  </ul>

  <div class="page-stripe"></div>
</main>
</body>
</html>
```